New website for a business that provides behaviour analysis

A new website that details the services that are provided around behaviour analysis for people with a disability through QPKV. There also needs to incorporate an about us and a staff page, Plus a referral form that is a google doc.
The business already has a web address that needs to be tailored.
Soft colours are preferred.
Do not have lots of pictures, keep them minimal.
A logo for the business is also needed to be incorporated, and this is a separate project that can be awarded to the website winner.
Website needs to be able to be used on WIX who will be the host for the design.

Target Market(s)

QPKV clients requiring behaviour support clician

Industry/Entity Type

Clinical behaviour support and analysis

Colors
00AB8E
00BBA5
67D7C9
C6EFE9
E9F9F6

Requirements
Must have
• Soft colours, preferable pale turquoise, minimal pictures, clean, sophisticated and classical look

```html
<!DOCTYPE html>
<html lang="en">
<head>
<meta charset="utf-8">
<title>Calmpath – Behaviour Analysis</title>
<link href="https://fonts.googleapis.com/css2?family=Bebas+Neue&family=Poppins:ital,wght@0,400;0,500;0,600;0,700;1,700&display=swap" rel="stylesheet">
<style>
:root{
  --green:#00AB8E;
  --teal:#00BBA5;
  --mint:#67D7C9;
  --pale:#C6EFE9;
  --ice:#E9F9F6;
  --ink:#1e1e1e;
  --text:#3a3a3a;
  --card:#f4f4f4;
  --footer:#2b2b2b;
  --white:#fff;
}
*{margin:0;padding:0;box-sizing:border-box}
html,body{width:1200px;height:4808px;overflow:hidden}
body{position:relative;font-family:'Poppins',sans-serif;color:var(--text);background:var(--white)}
.abs{position:absolute}
.brand{position:absolute;display:flex;align-items:center;gap:10px;font-family:'Poppins',sans-serif;font-weight:700;font-size:32px;line-height:40px;color:var(--green)}
.brand-mark{width:14px;height:14px;border-radius:50%;background:var(--green)}
.nav a{position:absolute;top:56px;font-size:14px;font-weight:600;color:#444;text-decoration:none;letter-spacing:.3px}
.nav a.active{color:var(--green)}
.btn{position:absolute;display:flex;align-items:center;justify-content:center;background:linear-gradient(90deg,var(--green),var(--teal));color:var(--white);border-radius:40px;font-weight:600;text-decoration:none}
.photo{position:absolute}
.hero-title{font-family:'Bebas Neue',sans-serif;font-size:72px;line-height:62px;color:var(--ink)}
.hero-title span{color:var(--green)}
.hero-lead{font-size:27px;line-height:40px;color:var(--ink);font-weight:500}
.h2{font-size:46px;font-weight:700;color:var(--ink)}
.svc-title{font-size:32px;line-height:42px;font-weight:700;font-style:italic;color:var(--green)}
.body-copy{font-size:15.6px;line-height:28px;color:#444}
.staff-band{background:var(--green)}
.avatar{position:absolute;width:243px;height:243px;border-radius:50%;top:3322px}
.staff-name{position:absolute;top:3588px;width:260px;text-align:center;font-size:22px;font-weight:600;color:var(--white)}
.staff-bio{position:absolute;top:3634px;width:240px;text-align:center;font-size:14px;line-height:26px;color:var(--ice);white-space:nowrap}
.staff-btn{position:absolute;top:3732px;width:131px;height:38px;border:1.5px solid var(--white);border-radius:20px;color:var(--white);font-size:14px;font-weight:500;display:flex;align-items:center;justify-content:center}
.field{position:absolute;left:112px;width:457px;height:52px;border:1px solid #ddd;border-radius:26px;background:var(--white);font-size:14px;color:#777;padding:16px 28px}
.footer h4{font-size:20px;font-weight:600;color:var(--green);position:absolute;top:4532px}
.footer .col{position:absolute;top:4572px;font-size:15px;line-height:33px;color:var(--white)}
.social{position:absolute;top:4580px;width:24px;height:24px;border-radius:50%;background:var(--white)}
</style>
</head>
<body>

<header>
  <div class="brand" style="left:75px;top:45px;"><span class="brand-mark"></span>Calmpath</div>
  <nav class="nav">
    <a class="active" style="left:302px">HOME</a>
    <a style="left:386px">ABOUT US</a>
    <a style="left:500px">SERVICES</a>
    <a style="left:612px">STAFF</a>
    <a style="left:698px">LATEST NEWS</a>
    <a style="left:840px">CONTACT US</a>
  </nav>
  <a class="btn" style="left:967px;top:41px;width:158px;height:49px;font-size:14px;">REFERRAL FORM</a>
</header>

<section class="hero abs" style="left:0;top:121px;width:1200px;height:709px;">
  <div class="photo" role="img" aria-label="Team meeting around an office table with a colleague in a wheelchair" style="left:0;top:0;width:1200px;height:709px;background:linear-gradient(90deg,#e9ecee 0%,#e4e7ea 30%,#b9bcc0 55%,#8a8c8f 75%,#6f7174 100%);"></div>
  <h1 class="hero-title abs" style="left:75px;top:234px;">Welcome to<br><span>Behaviour Analysis</span></h1>
  <p class="hero-lead abs" style="left:75px;top:360px;width:560px;">Excepteur sint occaecat cupidatat non proident, sunt in culpa qui.</p>
  <a class="btn" style="left:75px;top:461px;width:184px;height:64px;font-family:'Bebas Neue',sans-serif;font-size:26px;font-weight:400;">READ MORE</a>
</section>

<section class="about abs" style="left:75px;top:912px;width:1050px;height:441px;background:var(--card);border-radius:24px;">
  <div class="photo" role="img" aria-label="Researcher wearing an EEG sensor cap" style="left:28px;top:40px;width:483px;height:364px;border-radius:28px;background:linear-gradient(135deg,#2b4d6c,#16283d 60%,#0d1a2a);"></div>
  <h2 class="h2 abs" style="left:541px;top:36px;">About Us</h2>
  <p class="body-copy abs" style="left:541px;top:100px;width:490px;line-height:30.5px;font-size:15px;">Sed ut perspiciatis unde omnis iste natus error sit voluptatem accusantium doloremque laudantium, totam rem aperiam, eaque ipsa quae ab illo inventore veritatis et quasi architecto beatae vitae dicta sunt explicabo. Nemo enim ipsam voluptatem quia voluptas sit aspernatur aut odit aut fugit, sed quia consequuntur magni dolores eos qui ratione voluptatem sequi nesciunt.</p>
  <a class="btn" style="left:541px;top:342px;width:177px;height:56px;font-size:15px;">READ MORE</a>
</section>

<h2 class="h2 abs" style="left:0;width:1200px;text-align:center;top:1408px;">Our Services</h2>

<section class="services">
  <div class="photo" role="img" aria-label="Clinician taking notes during a session with a client" style="left:0;top:1523px;width:586px;height:465px;border-radius:0 24px 24px 0;background:linear-gradient(135deg,#b9a38e,#8f8275 50%,#4f5862);"></div>
  <h3 class="svc-title abs" style="left:616px;top:1576px;">Excepteur sint occaecat<br>cupidatat</h3>
  <p class="body-copy abs" style="left:616px;top:1670px;width:520px;">INemo enim ipsam voluptatem quia voluptas sit aspernatur aut odit aut fugit, sed quia consequuntur magni dolores eos qui ratione voluptatem sequi nesciunt. Neque porro quisquam est, qui dolorem ipsum quia dolor sit amet, consectetur, adipisci velit, sed quia non numquam eius modi tempora incidunt ut labore et dolore magnam aliquam quaerat voluptatem.</p>
  <a class="btn" style="left:616px;top:1864px;width:184px;height:56px;font-size:20px;">Read More</a>

  <h3 class="svc-title abs" style="left:75px;top:2111px;">Excepteur sint occaecat<br>cupidatat</h3>
  <p class="body-copy abs" style="left:75px;top:2205px;width:520px;">INemo enim ipsam voluptatem quia voluptas sit aspernatur aut odit aut fugit, sed quia consequuntur magni dolores eos qui ratione voluptatem sequi nesciunt. Neque porro quisquam est, qui dolorem ipsum quia dolor sit amet, consectetur, adipisci velit, sed quia non numquam eius modi tempora incidunt ut labore et dolore magnam aliquam quaerat voluptatem.</p>
  <a class="btn" style="left:75px;top:2400px;width:184px;height:56px;font-size:20px;">Read More</a>
  <div class="photo" role="img" aria-label="Group discussion led by a man in a checked shirt" style="left:616px;top:2058px;width:584px;height:465px;border-radius:24px 0 0 24px;background:linear-gradient(135deg,#d8dcdf,#9aa3ab 50%,#5a6470);"></div>

  <div class="photo" role="img" aria-label="Presenter in a wheelchair at a whiteboard with colleagues" style="left:0;top:2600px;width:586px;height:464px;border-radius:0 24px 24px 0;background:linear-gradient(135deg,#eef0ef,#c7c8c2 50%,#8f8a80);"></div>
  <h3 class="svc-title abs" style="left:616px;top:2646px;">Excepteur sint occaecat<br>cupidatat</h3>
  <p class="body-copy abs" style="left:616px;top:2740px;width:520px;">INemo enim ipsam voluptatem quia voluptas sit aspernatur aut odit aut fugit, sed quia consequuntur magni dolores eos qui ratione voluptatem sequi nesciunt. Neque porro quisquam est, qui dolorem ipsum quia dolor sit amet, consectetur, adipisci velit, sed quia non numquam eius modi tempora incidunt ut labore et dolore magnam aliquam quaerat voluptatem.</p>
  <a class="btn" style="left:616px;top:2950px;width:184px;height:56px;font-size:20px;">Read More</a>
</section>

<section class="staff-band abs" style="left:0;top:3154px;width:1200px;height:873px;">
  <h2 class="h2 abs" style="left:0;width:1200px;text-align:center;top:72px;color:var(--white);">Our Staff</h2>
</section>
<div class="avatar" role="img" aria-label="Staff portrait" style="left:74px;background:linear-gradient(160deg,#6b5a4a,#2a2522);"></div>
<div class="avatar" role="img" aria-label="Staff portrait" style="left:343px;background:linear-gradient(160deg,#d9dde0,#8a9aa8);"></div>
<div class="avatar" role="img" aria-label="Staff portrait" style="left:613px;background:linear-gradient(160deg,#7d6f63,#2f3238);"></div>
<div class="avatar" role="img" aria-label="Staff portrait" style="left:882px;background:linear-gradient(160deg,#e3e5e8,#9a8a78);"></div>

<div class="staff-name" style="left:66px">Name Heading</div>
<div class="staff-name" style="left:335px">Name Heading</div>
<div class="staff-name" style="left:605px">Name Heading</div>
<div class="staff-name" style="left:874px">Name Heading</div>
<p class="staff-bio" style="left:76px">Nemo enim ipsam voluptat<br>em quia voluptas sit aspe<br>natur aut odit...</p>
<p class="staff-bio" style="left:345px">Nemo enim ipsam voluptat<br>em quia voluptas sit aspe<br>natur aut odit...</p>
<p class="staff-bio" style="left:615px">Nemo enim ipsam voluptat<br>em quia voluptas sit aspe<br>natur aut odit...</p>
<p class="staff-bio" style="left:884px">Nemo enim ipsam voluptat<br>em quia voluptas sit aspe<br>natur aut odit...</p>
<div class="staff-btn" style="left:130px">Read More</div>
<div class="staff-btn" style="left:399px">Read More</div>
<div class="staff-btn" style="left:669px">Read More</div>
<div class="staff-btn" style="left:938px">Read More</div>

<section class="contact abs" style="left:75px;top:3867px;width:1050px;height:546px;background:var(--card);border-radius:24px;box-shadow:0 6px 24px rgba(0,0,0,.15);">
  <h2 class="h2 abs" style="left:35px;top:30px;">Contact Us</h2>
  <div class="photo" role="img" aria-label="Older woman and young man looking at a tablet together" style="left:541px;top:43px;width:487px;height:459px;border-radius:22px;background:linear-gradient(135deg,#8c8f93,#b88d4a 45%,#5d4f44 75%,#3b3f46);"></div>
</section>
<div class="field" style="top:3975px">Name</div>
<div class="field" style="top:4042px">Email Address</div>
<div class="field" style="top:4109px">Phone No</div>
<div class="field" style="top:4180px;height:120px;border-radius:26px;">Message</div>
<a class="btn" style="left:112px;top:4315px;width:457px;height:54px;font-size:20px;">Submit</a>

<footer class="footer abs" style="left:0;top:4485px;width:1200px;height:323px;background:var(--footer);"></footer>
<div class="brand" style="left:75px;top:4596px;"><span class="brand-mark"></span>Calmpath</div>
<p class="abs" style="left:75px;top:4690px;font-size:13px;line-height:24px;color:var(--white);">Copyright © 2024CompanyName<br>All Rights Reserved.</p>
<div class="footer">
  <h4 style="left:358px">Quick Links</h4>
  <div class="col" style="left:358px">Home<br>About Us<br>Services<br>Staff<br>Latest News<br>Contact Us</div>
  <h4 style="left:616px">Contact Info</h4>
  <div class="col" style="left:616px;line-height:28px;">48 Harbour Lane Suite 12,<br>Brookfield 20415, United State<br><span style="display:block;margin-top:10px">+100-555-0142</span><span style="display:block;margin-top:10px">hello@calmpathclinic.com</span></div>
  <h4 style="left:894px">Follow Us</h4>
  <div class="social" style="left:894px"></div>
  <div class="social" style="left:930px"></div>
  <div class="social" style="left:972px"></div>
  <div class="social" style="left:1016px"></div>
  <div class="social" style="left:1066px"></div>
</div>

</body>
</html>
```